Small legal and financial translation company needs Squarespace website, brochure and logo

Hello,
We are Lumarin Services (www.lumarinservices-example.com), a boutique legal and financial translation company. We offer our services mainly to Spanish customers. Our primary line of business is the translation of financial statements, but we translate a wide variety legal and financial texts.
The project we are offering comprises three parts: a redo of the current website, an informational brochure for potential customer and a logo design. These three parts should provide a consistent image. We would develop content soon.
We are looking for a website that would look like a typical law firm website, nothing too fancy. Right now, it is in English, Spanish and French, although the new site need only be in English and Spanish. There must be good toggling between the English and Spanish versions. There would be no need for tie-ins to social media and it would not contain a blog. Basically, a static site. We aren't interesting in driving traffic to the site or SEO, as we will contact nearly all potential customers beforehand. The website must be built in Squarespace to enable a smooth transition. The content would be similar to the current page, we'll be working on the exact content, but a rough draft is attached.
The brochure will be some three pages and would introduce the company to potential customers, using similar images as the website and the logo to be designed.
The only specifications for the logo is, as the website and brochure, it convey a sense of security and trust.
Feel free to ask with any questions as this is the first time we have used this platform.
Thank you!
Updates

I've added a more or less final version for the text in the brochure and updated the brief. Added Wednesday, June 10, 2015

Target Market(s)

Spanish law firms, auditors, accountants, banks, investment firms

Industry/Entity Type

Finance

Logo Text

Lumarin Services

Number of Pages Required

5+ page

Font styles to use
Serif

Requirements
Must have
• The website must be built in Squarespace and have a good option to toggle between English and Spanish versions.
• Brochure must be in both English and Spanish, I'm attaching a rough draft of the information that it will probably have. This should give an idea about what to include and the spacing. I will update it to include the final information.
Nice to have
• Would be nice to have some quality finance- and legal-related images
Should not have
• Vibrant colours

```html
<!DOCTYPE html>
<html lang="en">
<head>
<meta charset="utf-8">
<title>Lumarin Services – Pricing</title>
<link href="https://fonts.googleapis.com/css2?family=Cormorant+Garamond:wght@400;500&family=Cormorant+SC:wght@500&display=swap" rel="stylesheet">
<style>
  :root {
    --backdrop: #cccccc;
    --paper: #ffffff;
    --brand-blue: #29417d;
    --ink-black: #000000;
    --body-ink: #111111;
    --photo-light: #e4e6ea;
    --photo-mid: #9a9ea8;
    --photo-dark: #5a5f6b;
  }
  html, body {
    margin: 0;
    padding: 0;
    width: 1200px;
    height: 1200px;
    overflow: hidden;
    background: var(--backdrop);
  }
  .brochure-page {
    position: absolute;
    left: 268px;
    top: 110px;
    width: 699px;
    height: 991px;
    background: var(--paper);
    overflow: hidden;
  }
  .hero-photo {
    position: absolute;
    left: 0;
    top: 40px;
    width: 699px;
    height: 405px;
    background: linear-gradient(180deg, var(--paper) 0%, var(--photo-light) 20%, var(--photo-mid) 50%, var(--photo-dark) 100%);
  }
  .band-shapes {
    position: absolute;
    left: 0;
    top: 0;
    width: 699px;
    height: 991px;
  }
  .section-title {
    position: absolute;
    left: 41px;
    top: 521px;
    margin: 0;
    font-family: "Cormorant SC", serif;
    font-weight: 500;
    font-size: 37px;
    letter-spacing: 1px;
    color: var(--brand-blue);
  }
  .section-body {
    position: absolute;
    left: 47px;
    top: 576px;
    width: 612px;
    margin: 0;
    font-family: "Cormorant Garamond", serif;
    font-weight: 500;
    font-size: 14.4px;
    line-height: 19.4px;
    letter-spacing: -0.5px;
    word-spacing: -0.6px;
    font-variant-numeric: lining-nums;
    text-align: justify;
    color: var(--body-ink);
  }
  .site-address {
    position: absolute;
    left: 24px;
    top: 952px;
    margin: 0;
    font-family: "Cormorant Garamond", serif;
    font-weight: 500;
    font-size: 18px;
    color: var(--paper);
  }
</style>
</head>
<body>
  <main class="brochure-page">
    <div class="hero-photo" role="img" aria-label="Photo of a businessman offering a handshake in front of a large group of business people"></div>

    <svg class="band-shapes" viewBox="0 0 699 991" aria-hidden="true">
      <polygon points="372,412 699,365 699,445 617,448" fill="var(--ink-black)"/>
      <polygon points="557,383 656,326 656,380" fill="var(--brand-blue)"/>
      <polygon points="0,365 612,449 0,477" fill="var(--brand-blue)"/>
      <line x1="0" y1="363" x2="617" y2="450" stroke="var(--paper)" stroke-width="3"/>
      <polygon points="0,923 699,991 0,991" fill="var(--brand-blue)"/>
      <polygon points="364,956 699,923 699,988" fill="var(--ink-black)"/>
      <line x1="364" y1="957" x2="699" y2="990" stroke="var(--paper)" stroke-width="2"/>
      <polygon points="532,937 660,880 672,923" fill="var(--brand-blue)"/>
    </svg>

    <h1 class="section-title">Pricing</h1>
    <p class="section-body">Our prices take into account a wide variety of factors based on each individual job to be carried out. Urgency, formatting, past experience, technical complexity and many other factors go into preparing a quote tailored to customers' needs. We are always happy to discuss pricing with our customers, although a basic starting point for any job stands around EUR 0.085/word.</p>

    <p class="site-address">www.lumarinservices-example.com</p>
  </main>
</body>
</html>
```